Structural Engineering Business Card

Brookvane Drafting does residential house plans for clients in Central Florida. Would like simple but elegant business card that is appropriate for a house plan engineering company. Prefer black business card with black/white them but open to other shades of blue. I uploaded a sample card that I came across that looked good but please come up with your own creative designs.

Contact Information for Business Card

Name, Title, Phone, Email, Address, website

```html
<!DOCTYPE html>
<html lang="en">
<head>
<meta charset="utf-8">
<title>Brookvane Drafting – Business Card</title>
<link href="https://fonts.googleapis.com/css2?family=Poppins:wght@400;700;800&display=swap" rel="stylesheet">
<style>
  :root {
    --ink: #0b0b0c;
    --card-dark: #0d0d0f;
    --card-dark-2: #151517;
    --paper: #ffffff;
    --stage: #d9d9d9;
    --rule: #8a8a8a;
  }
  * { margin: 0; padding: 0; box-sizing: border-box; }
  html, body { width: 1200px; height: 1200px; overflow: hidden; }
  body {
    background: var(--stage);
    font-family: "Poppins", sans-serif;
    position: relative;
  }
  .card {
    position: absolute;
    top: 303px;
    width: 368px;
    height: 594px;
  }
  .card--back {
    left: 200px;
    background: linear-gradient(160deg, var(--card-dark-2) 0%, var(--card-dark) 60%, #080809 100%);
  }
  .card--front {
    left: 600px;
    background: var(--paper);
    color: var(--ink);
    text-align: center;
  }
  .brand {
    position: absolute;
    left: 0; right: 0;
    display: flex;
    align-items: center;
    justify-content: center;
    gap: 12px;
  }
  .brand__mark { width: 14px; height: 14px; flex: none; }
  .brand__name {
    font-weight: 800;
    font-size: 27px;
    line-height: 1.05;
    letter-spacing: 0.5px;
    text-align: left;
  }
  .card--back .brand { top: 470px; }
  .card--back .brand__mark { background: var(--paper); }
  .card--back .brand__name { color: var(--paper); }
  .card--front .brand { top: 148px; }
  .card--front .brand__mark { background: var(--ink); }
  .card--front .brand__name { color: var(--ink); }

  .person { position: absolute; top: 336px; left: 0; right: 0; }
  .person__name { font-weight: 700; font-size: 20px; letter-spacing: 0.3px; line-height: 1.2; }
  .person__title { font-weight: 400; font-size: 15.5px; line-height: 1.3; }

  .icons {
    position: absolute; top: 396px; left: 0; right: 0;
    display: flex; align-items: center; justify-content: center; gap: 4px;
  }
  .icons__rule { width: 52px; height: 1px; background: var(--rule); margin: 0 4px; }
  .icon { width: 25px; height: 25px; background: var(--ink); border-radius: 3px; display: flex; align-items: center; justify-content: center; }
  .icon svg { width: 17px; height: 17px; }

  .contact { position: absolute; top: 428px; left: 0; right: 0; font-size: 16px; line-height: 21px; }
  .divider { position: absolute; top: 506px; left: 88px; width: 195px; height: 1px; background: var(--rule); }
  .address { position: absolute; top: 518px; left: 0; right: 0; font-size: 16px; line-height: 21px; }
</style>
</head>
<body>
  <section class="card card--back">
    <div class="brand">
      <span class="brand__mark"></span>
      <span class="brand__name">BROOKVANE<br>DRAFTING</span>
    </div>
  </section>

  <section class="card card--front">
    <div class="brand">
      <span class="brand__mark"></span>
      <span class="brand__name">BROOKVANE<br>DRAFTING</span>
    </div>

    <div class="person">
      <p class="person__name">DANIEL HARPER</p>
      <p class="person__title">Managing Director</p>
    </div>

    <div class="icons">
      <span class="icons__rule"></span>
      <span class="icon" aria-label="Phone">
        <svg viewBox="0 0 24 24" fill="none" stroke="#fff" stroke-width="2" stroke-linejoin="round"><path d="M3 9c0-2 2-4 9-4s9 2 9 4v2h-5V9H8v2H3z"/><path d="M6 12h12l1 7H5z"/><circle cx="12" cy="15.5" r="1.5"/></svg>
      </span>
      <span class="icon" aria-label="Email">
        <svg viewBox="0 0 24 24" fill="none" stroke="#fff" stroke-width="2"><rect x="3" y="6" width="18" height="12"/><path d="M3 6l9 7 9-7"/></svg>
      </span>
      <span class="icon" aria-label="Website">
        <svg viewBox="0 0 24 24" fill="none" stroke="#fff" stroke-width="2"><circle cx="12" cy="12" r="8"/><path d="M4 12h16M12 4c3 3 3 13 0 16M12 4c-3 3-3 13 0 16"/></svg>
      </span>
      <span class="icons__rule"></span>
    </div>

    <div class="contact">
      <p>044-555 010 234</p>
      <p>info@brookvane.com</p>
      <p>www.brookvanedrafting.com</p>
    </div>

    <div class="divider"></div>

    <div class="address">
      <p>218, Orchard Lane</p>
      <p>32801, Orlando FL</p>
    </div>
  </section>
</body>
</html>
```